Web Design Project for Audio-Visual & Video Communications Business

We are currently busy with our new Wordpress website and require cutting-edge designs for our Home page. The intro images on the Home Page must give our visitors a quick overview of the services that we sell. These are broken down into 3 different services:

1. Audio-Visual (These include projectors, audio systems, projector screens, specialised brackets, Veltrane control systems, etc)

2. Video Communications products (We sell Marivox and TrueBand equipment)

3. Online Shop (We need the best design to attract our existing and new visitors. The current design on the website was only done to show you what we have on offer)

We prefer to use the current theme but would like you to start building on top of this. This will be an ongoing project during 2013 to ensure that we keep the site fresh and updated.

Target Market(s)

We market our business to the Corporate, Education and Hospitality markets. We do however have individuals that will buy equipment online.

Industry/Entity Type

Building

Requirements
Must have
• The design must consist of 3 independent pages. We have several sliders that we can use on the Home page so you can decide if images and text must be visible at different times.
Nice to have
• You can visit the current draft website for the current look and feel. If you have completely new ideas we might consider them. Visit the site at www.linkwavegroup.co.za.

```html
<!DOCTYPE html>
<html lang="en">
<head>
<meta charset="utf-8">
<title>LinkWave – Home</title>
<link href="https://fonts.googleapis.com/css2?family=Source+Sans+3:wght@400;600;700&display=swap" rel="stylesheet">
<style>
:root{
  --green:#b3c74e;
  --green-dark:#8ea72a;
  --green-card:#97af34;
  --green-btn:#86a521;
  --ink:#333;
  --ink-soft:#666;
  --grey-band:#e6e6e6;
  --card-grey:#eaeaea;
  --white:#fff;
}
*{box-sizing:border-box;margin:0;padding:0}
html,body{width:990px;height:1200px;overflow:hidden;background:var(--white)}
body{font-family:"Source Sans 3",sans-serif;color:var(--ink);position:relative}
a{color:inherit;text-decoration:none}

/* header */
.site-header{position:absolute;left:0;top:0;width:990px;height:103px}
.brand{position:absolute;left:128px;top:52px;display:flex;align-items:center;gap:6px;font-size:18px;font-weight:700;color:var(--green-dark)}
.brand-dot{width:12px;height:12px;border-radius:50%;background:#666}
.utility-nav{position:absolute;right:117px;top:31px;font-size:9px;color:var(--ink)}
.utility-nav span{margin:0 4px;color:#999}
.main-nav{position:absolute;top:70px;left:0;width:990px;font-size:15px}
.main-nav a{position:absolute;white-space:nowrap}

/* hero */
.hero{position:absolute;left:0;top:103px;width:990px;height:299px;background:var(--green)}
.slider{position:absolute;left:120px;top:8px;width:756px;height:258px;border-radius:5px;overflow:hidden;
  box-shadow:0 8px 14px rgba(0,0,0,.18)}
.slider-photo{position:absolute;inset:0;background:linear-gradient(180deg,#cfd0d4 0%,#d9dadd 60%,#eef1f2 62%,#f7f9f9 100%)}
.slider-photo .product-area{position:absolute;left:38px;top:80px;width:350px;height:170px;border-radius:20px;
  background:radial-gradient(ellipse at 50% 50%,#2a2a2c 0%,#1a1a1c 55%,rgba(20,20,22,0) 72%)}
.slide-copy{position:absolute;left:432px;top:76px;width:280px}
.slide-copy h1{font-size:25px;font-weight:600;color:#333;line-height:1}
.slide-copy h2{font-size:10.5px;font-weight:600;color:#444;margin-top:18px}
.slide-copy p{font-size:10px;color:#555;margin-top:14px;line-height:1.35}
.slider-dots{position:absolute;left:466px;top:277px;display:flex;gap:7px}
.slider-dots i{width:9px;height:9px;border-radius:50%;background:#fff;border:1px solid #ddd}
.slider-dots i.active{background:#111;border-color:#111}

/* service teasers */
.teaser{position:absolute;top:417px;width:236px;height:236px;background:var(--white);border:1px solid #e4e4e4;border-radius:3px;
  box-shadow:0 1px 3px rgba(0,0,0,.06)}
.teaser h3{height:38px;padding:11px 0 0 19px;font-size:16.5px;font-weight:600;color:#333;background:linear-gradient(#fff,#f4f4f4);border-bottom:1px solid #eee}
.teaser-photo{position:absolute;left:15px;top:47px;width:207px;height:104px;border-radius:3px}
.photo-audio{background:linear-gradient(135deg,#0a0c3a 0%,#1d39c4 45%,#0a0e4f 100%)}
.photo-video{background:linear-gradient(135deg,#2a4d7a 0%,#6d95c4 40%,#1b1f2a 70%,#0e0f14 100%)}
.teaser p{position:absolute;left:18px;top:158px;width:200px;font-size:9.5px;color:var(--ink-soft);line-height:1.55}
.btn-learn{position:absolute;left:16px;top:198px;padding:4px 11px;font-size:8.5px;font-weight:700;color:#fff;
  background:linear-gradient(#9cbd32,var(--green-btn));border-radius:2px}
.teaser-shop{background:var(--green-card);border-color:var(--green-card)}
.teaser-shop h3{color:#fff;background:linear-gradient(#a3bb3f,#97af34);border-bottom:0}
.shop-photo{position:absolute;left:13px;top:46px;width:216px;height:106px;background:#fff;border-radius:3px}
.shop-photo .product-area{position:absolute;left:58px;top:12px;width:100px;height:80px;border-radius:6px;
  background:linear-gradient(#3a3a3a,#1b1b1b 60%,#d8d8d8 62%,#fff)}
.shop-photo svg{position:absolute;top:40px}
.product-name{position:absolute;left:18px;top:161px;font-size:13.5px;font-weight:600;color:#4a5c10}
.product-desc{position:absolute;left:18px;top:180px;font-size:9.5px;color:#e8efcf}
.btn-buy{position:absolute;left:19px;top:199px;padding:4px 13px;font-size:8.5px;font-weight:700;color:#fff;
  background:#a9c04f;border-radius:2px}

/* welcome */
.welcome{position:absolute;left:0;top:672px;width:990px;height:154px;background:var(--grey-band)}
.welcome h2{position:absolute;left:116px;top:19px;font-size:19.5px;font-weight:600;color:#444}
.welcome p{position:absolute;left:116px;top:54px;width:756px;font-size:8.6px;line-height:1.38;color:#333}

/* services */
.service{position:absolute;top:846px;width:184px;height:184px;background:var(--card-grey);border-radius:4px;
  box-shadow:0 2px 2px rgba(0,0,0,.12)}
.service h3{position:absolute;left:16px;top:16px;font-size:14.5px;font-weight:400;color:#333;white-space:nowrap}
.service p{position:absolute;left:16px;top:49px;width:154px;font-size:8.6px;line-height:1.38;color:#444}
.service .view-more{position:absolute;left:16px;top:153px;font-size:8.6px;color:#444}

/* footer */
.site-footer{position:absolute;left:16px;top:1045px;width:974px;height:155px;background:var(--green)}
.newsletter{position:absolute;left:100px;top:25px;width:212px;height:93px;background:#f3f3f3;padding:4px;
  background-image:repeating-linear-gradient(135deg,#c23b3b 0 5px,#f3f3f3 5px 10px,#2f5ca8 10px 15px,#f3f3f3 15px 20px)}
.newsletter-inner{width:100%;height:100%;background:#f6f6f6;padding:8px 11px 0 13px}
.newsletter h4{font-size:13px;font-weight:600;color:#666}
.signup{margin-top:5px;display:flex;height:21px;border:1px solid #ccc;background:#fff}
.signup span{flex:1;font-size:9.5px;color:#888;padding:4px 0 0 8px}
.signup b{background:#111;color:#fff;font-size:9px;padding:4px 8px 0;border-radius:2px;margin:1px}
.newsletter small{display:block;margin-top:5px;font-size:9px;color:#777;line-height:1.25}
.footer-col{position:absolute;top:24px;font-size:10.5px;color:#1e1e1e}
.footer-col h5{font-size:11.5px;font-weight:600;margin-bottom:14px}
.footer-col li{list-style:none;line-height:20px}
.contact-col li{line-height:15.5px}
.contact-col em{font-style:normal;display:inline-block;width:27px}
.social{display:flex;gap:6px;margin:-2px 0 14px}
.social i{width:26px;height:26px;border-radius:50%;background:#fff;border:2px solid #e3e9cc;box-shadow:0 1px 2px rgba(0,0,0,.2)}
.social i:nth-child(1){background:#f39a2f}
.social i:nth-child(2){background:#4fb3e4}
.social i:nth-child(3){background:#2d5aa8}
.social i:nth-child(4){background:#1fa7e0}
.legal{line-height:18px}
</style>
</head>
<body>

<header class="site-header">
  <a class="brand" href="#"><span class="brand-dot"></span>LinkWave</a>
  <nav class="utility-nav"><a href="#">Shop</a><span>|</span><a href="#">My Account</a><span>|</span><a href="#">Checkout</a><span>|</span><a href="#">0 items - R0</a></nav>
  <nav class="main-nav">
    <a href="#" style="left:503px">Home</a>
    <a href="#" style="left:578px">Shop</a>
    <a href="#" style="left:649px">About us</a>
    <a href="#" style="left:742px">Blog</a>
    <a href="#" style="left:808px">Contact us</a>
  </nav>
</header>

<section class="hero">
  <div class="slider">
    <div class="slider-photo" role="img" aria-label="Black HD projector on a white surface">
      <div class="product-area"></div>
    </div>
    <div class="slide-copy">
      <h1>Secure Online Shopping</h1>
      <h2>Lorem Ipsum is simply dummy text</h2>
      <p>Typesetting industry. Lorem Ipsum has been the industry's standard dummy text ever since the 1500s, when an unknown printer took a galley of type and scrambled it to make a type specimen book.</p>
    </div>
  </div>
  <div class="slider-dots"><i class="active"></i><i></i><i></i><i></i></div>
</section>

<article class="teaser" style="left:116px">
  <h3>Audio Visual</h3>
  <div class="teaser-photo photo-audio" role="img" aria-label="Blue illuminated audio amplifier display"></div>
  <p>Duis tincidunt quis dui viverra vestibulum. Suspendisse aliquam dui.</p>
  <a class="btn-learn" href="#">Learn More</a>
</article>

<article class="teaser" style="left:378px">
  <h3>Video Communications</h3>
  <div class="teaser-photo photo-video" role="img" aria-label="Flat screen display showing a video wall"></div>
  <p>Duis tincidunt quis dui viverra vestibulum. Suspendisse aliquam dui.</p>
  <a class="btn-learn" href="#" style="top:196px">Learn More</a>
</article>

<article class="teaser teaser-shop" style="left:639px">
  <h3>Online shopping</h3>
  <div class="shop-photo">
    <svg style="left:12px" width="16" height="26" viewBox="0 0 16 26"><path d="M13 2 3 13l10 11" fill="none" stroke="#aaa" stroke-width="2"/></svg>
    <div class="product-area" role="img" aria-label="Home theatre speakers and receiver"></div>
    <svg style="right:12px" width="16" height="26" viewBox="0 0 16 26"><path d="M3 2l10 11L3 24" fill="none" stroke="#aaa" stroke-width="2"/></svg>
  </div>
  <div class="product-name">Product Name</div>
  <div class="product-desc">Duis tincidunt quis dui viverra vestibulum.</div>
  <a class="btn-buy" href="#">BUY NOW</a>
</article>

<section class="welcome">
  <h2>Welcome to LinkWave</h2>
  <p>Lorem Ipsum is simply dummy text of the printing and typesetting industry. Lorem Ipsum has been the industry's standard dummy text ever since the 1500s, when an unknown printer took a galley of type and scrambled it to make a type specimen book. It has survived not only five centuries, but also the leap into electronic typesetting, remaining essentially unchanged. It was popularised in the 1960s with the release of Letraset sheets containing Lorem Ipsum passages, and more recently with desktop publishing software like Aldus PageMaker including versions of Lorem IpsumLorem Ipsum is simply dummy text of the printing and typesetting industry. Lorem Ipsum has been the industry's standard dummy text ever since the 1500s, when an unknown printer took a galley of type and scrambled it to make a type specimen book. It has survived not only five centuries, but also the leap into electronic typesetting, remaining essentially unchanged. It was popularised in the 1960s with the release of Letraset sheets containing Lorem Ipsum passages, and more recently with desktop publishing software like Aldus PageMaker including versions of Lorem Ipsum.</p>
</section>

<article class="service" style="left:116px">
  <h3>Consultation &amp; Design</h3>
  <p>Lorem Ipsum is simply dummy text of the printing and typesetting industry. Lorem Ipsum has been the industry's standard dummy text ever since the 1500s, when an unknown printer took a galley of type and scrambled it to make a type specimen book.</p>
  <a class="view-more" href="#">View More</a>
</article>
<article class="service" style="left:308px">
  <h3 style="top:14px">Project Management</h3>
  <p>Lorem Ipsum is simply dummy text of the printing and typesetting industry. Lorem Ipsum has been the industry's standard dummy text ever since the 1500s, when an unknown printer took a galley of type and scrambled it to make a type specimen book.</p>
  <a class="view-more" href="#">View More</a>
</article>
<article class="service" style="left:499px">
  <h3 style="top:14px">Supply &amp; Installation</h3>
  <p>Lorem Ipsum is simply dummy text of the printing and typesetting industry. Lorem Ipsum has been the industry's standard dummy text ever since the 1500s, when an unknown printer took a galley of type and scrambled it to make a type specimen book.</p>
  <a class="view-more" href="#">View More</a>
</article>
<article class="service" style="left:690px">
  <h3 style="top:14px">Onsite Support Personal</h3>
  <p>Lorem Ipsum is simply dummy text of the printing and typesetting industry. Lorem Ipsum has been the industry's standard dummy text ever since the 1500s, when an unknown printer took a galley of type and scrambled it to make a type specimen book.</p>
  <a class="view-more" href="#">View More</a>
</article>

<footer class="site-footer">
  <div class="newsletter">
    <div class="newsletter-inner">
      <h4>Join Our Newsletter</h4>
      <div class="signup"><span>Enter Your Email Address</span><b>Sign Up</b></div>
      <small>Signup to receive invite to special events, parties, cooking demos, coupons</small>
    </div>
  </div>

  <div class="footer-col" style="left:349px">
    <h5>Company</h5>
    <ul><li>Privacy</li><li>Terms Of Use</li><li>Terms Of Trade</li><li>PO T&amp;C's</li></ul>
  </div>

  <div class="footer-col contact-col" style="left:468px">
    <h5>Contact Us</h5>
    <ul>
      <li>Level 9 210 Harbour Street</li>
      <li>Northgate Vic 3100</li>
      <li><em>T:</em>+61 3 5550 1313</li>
      <li><em>F:</em>+61 3 5550 1390</li>
      <li><em>E:</em>info@Company Name.com</li>
    </ul>
  </div>

  <div class="footer-col" style="left:652px">
    <h5>Follow Us Online</h5>
    <div class="social" aria-label="Social links"><i></i><i></i><i></i><i></i></div>
    <div class="legal">Privacy Policy | Terms of Services | Sitemap<br>Copyright © 2013. All Rights Reserved.</div>
  </div>
</footer>

</body>
</html>
```